Harrow Grading LLC business card design

Excavation company business cards

Contact Information for Business Card

Harrow Grading LLC cell phone 208-417-6290 office phone 208-319-4856 harrowgradingllc@maplecove.com Driveways, site prep, retaining walls, septic systems, rock delivery

Colors

Designer to choose colors to be used in the design.

```html
<!DOCTYPE html>
<html lang="en">
<head>
<meta charset="utf-8">
<title>Harrow Grading LLC – Business Card</title>
<link href="https://fonts.googleapis.com/css2?family=Arimo:wght@400;700&display=swap" rel="stylesheet">
<style>
  :root {
    --bg: #e9e9e8;
    --card-white: #ffffff;
    --orange: #e8702a;
    --orange-deep: #b9500f;
    --orange-light: #f29a5e;
    --grey: #555557;
    --line: #8a8a8c;
  }
  * { box-sizing: border-box; margin: 0; padding: 0; }
  html, body { width: 1200px; height: 802px; overflow: hidden; }
  body {
    background: var(--bg);
    font-family: "Arimo", Arial, sans-serif;
    position: relative;
  }
  .card {
    position: absolute;
    top: 252px;
    width: 525px;
    height: 300px;
    border-radius: 3px;
    box-shadow: 0 6px 18px rgba(0,0,0,0.12);
    overflow: hidden;
  }
  /* Front */
  .card-front { left: 45px; background: var(--card-white); }
  .brand {
    position: absolute;
    top: 58px; left: 0; right: 0;
    display: flex; align-items: center; justify-content: center; gap: 12px;
  }
  .brand-mark { width: 22px; height: 22px; background: var(--orange); }
  .brand-name {
    color: var(--orange); font-weight: 700; font-size: 34px; letter-spacing: 1px;
    text-transform: uppercase;
  }
  .person { position: absolute; left: 34px; top: 168px; }
  .person-name {
    color: var(--orange); font-weight: 700; font-size: 19px; text-transform: uppercase;
  }
  .person-role { color: var(--grey); font-size: 14px; margin-top: 3px; }
  .divider {
    position: absolute; left: 34px; right: 34px; top: 222px;
    height: 1.5px; background: var(--line);
  }
  .contacts {
    position: absolute; left: 34px; right: 34px; top: 236px;
    display: flex; align-items: center; gap: 16px;
    color: var(--grey); font-size: 13.5px; white-space: nowrap;
  }
  .contact { display: flex; align-items: center; gap: 6px; }
  .contact svg { width: 13px; height: 13px; flex: none; }

  /* Back */
  .card-back { left: 630px; background: var(--orange); }
  .back-brand {
    position: absolute; top: 30px; left: 30px;
    color: var(--orange-deep); font-weight: 700; font-size: 20px; text-transform: uppercase;
  }
  .services {
    position: absolute; left: 30px; top: 98px; list-style: none;
    color: #fde3d1; font-size: 17px; line-height: 1.45; text-transform: uppercase;
  }
  .services li::before {
    content: ""; display: inline-block; width: 6px; height: 6px; border-radius: 50%;
    background: #fde3d1; margin-right: 8px; vertical-align: middle;
  }
  .machine-art {
    position: absolute; right: 0; top: 0; width: 290px; height: 300px;
    background: linear-gradient(135deg, var(--orange-deep) 0%, var(--orange) 55%, var(--orange-light) 100%);
    opacity: 0.75;
  }
</style>
</head>
<body>
  <section class="card card-front">
    <div class="brand">
      <span class="brand-mark"></span>
      <span class="brand-name">Harrow Grading LLC</span>
    </div>
    <div class="person">
      <div class="person-name">Marcus Hale</div>
      <div class="person-role">Manager</div>
    </div>
    <div class="divider"></div>
    <div class="contacts">
      <span class="contact">
        <svg viewBox="0 0 14 14"><rect x="3" y="1" width="8" height="12" rx="1.5" fill="none" stroke="#e8702a" stroke-width="1.6"/><circle cx="7" cy="10.5" r="0.9" fill="#e8702a"/></svg>
        208-417-6290
      </span>
      <span class="contact">
        <svg viewBox="0 0 14 14"><path d="M3 1.5l2.5 0 1 3-1.6 1.2a7 7 0 0 0 3.4 3.4L9.5 7.5l3 1v2.5c0 .8-.7 1.5-1.5 1.5A10 10 0 0 1 1.5 3 1.5 1.5 0 0 1 3 1.5z" fill="#e8702a"/></svg>
        208-319-4856
      </span>
      <span class="contact">
        <svg viewBox="0 0 14 14"><rect x="1" y="3" width="12" height="8.5" fill="#e8702a"/><path d="M1 3l6 5 6-5" fill="none" stroke="#fff" stroke-width="1.2"/></svg>
        harrowgradingllc@maplecove.com
      </span>
    </div>
  </section>

  <section class="card card-back">
    <div class="machine-art" role="img" aria-label="Embossed illustration of an excavator digging in front of mountain peaks"></div>
    <div class="back-brand">Harrow Grading LLC</div>
    <ul class="services">
      <li>Driveways</li>
      <li>Site Prep</li>
      <li>Retaining Walls</li>
      <li>Septic Systems</li>
      <li>Rock Delivery</li>
    </ul>
  </section>
</body>
</html>
```